Website Home Page for Women's Health Medical Office

Redesign existing homepage for website using existing logo. Current website location is www.meadowcrestwomens.com. Please give it a modern, streamlined, playful feel.

Please give it a feminine feel and make it bright and cheerful using logo colors.

Target Market(s)

Women between the ages of 25-45

Industry/Entity Type

Medical Office

Coding

Coded - Design and coding required

Number of Pages Required

1 page

Font styles to use
Sans Serif
Other font styles liked:
• SEGOI UI script for text and GIL SANS for bold (or their equivilent)

Colors
E54698
E96AAD
F1A4CE
F9D9EA
FCEFF6

Requirements
Must have
• Existing logo. Logo Colors. Feminine, cheerful, simple design. all relevant contact information
Nice to have
• clean lines and streamlined look
Should not have
• Cluttered

```html
<!DOCTYPE html>
<html lang="en">
<head>
<meta charset="utf-8">
<title>Meadowcrest Women's – Personalized Medical Care for Women</title>
<link href="https://fonts.googleapis.com/css2?family=Poppins:ital,wght@0,400;0,500;0,600;0,700;1,400;1,700&display=swap" rel="stylesheet">
<style>
:root{
  --pink:#ec0f8c;
  --pink-2:#e54698;
  --pink-3:#e96aad;
  --pink-4:#f1a4ce;
  --pink-5:#f9d9ea;
  --pink-6:#fceff6;
  --ink:#111111;
  --text:#222222;
  --mark:#333333;
  --card:#f4f2f3;
  --dark:#1f1f1f;
  --white:#ffffff;
}
*{margin:0;padding:0;box-sizing:border-box}
html,body{width:1200px;height:2732px;overflow:hidden}
body{position:relative;background:var(--white);font-family:"Poppins",sans-serif;color:var(--text)}
.abs{position:absolute}
.top-wave{left:0;top:0}
.contact-bar{left:69px;top:91px;width:1062px;height:75px;background:var(--white);border-radius:14px;box-shadow:0 4px 18px rgba(0,0,0,.12);display:flex;align-items:center;justify-content:space-around;padding:0 20px;font-size:14.5px;font-weight:500;color:#333}
.contact-bar span{display:flex;align-items:center;gap:8px;white-space:nowrap}
.contact-bar svg{flex:none}
.brand{left:91px;top:238px;display:flex;align-items:center;gap:8px;font-weight:700;font-size:24px;color:var(--mark);line-height:1}
.brand-dot{width:12px;height:12px;border-radius:50%;background:var(--pink)}
.nav{left:517px;top:245px;display:flex;gap:38px;font-size:18px;font-weight:500;color:var(--ink)}
.welcome h1{left:101px;top:338px;font-size:39px;font-weight:700;line-height:48px;color:var(--ink)}
.welcome-copy{left:100px;top:506px;width:527px;font-size:14.6px;line-height:23px;text-align:justify}
.welcome-copy p+p{margin-top:23px}
.portrait{left:715px;top:394px;width:394px;height:394px;border-radius:50%;background:radial-gradient(circle at 50% 40%,#f4c7de 0%,var(--pink-3) 45%,var(--pink) 100%)}
.accept{left:92px;top:950px}
.accept .kicker{font-size:28px;line-height:38px;color:var(--ink)}
.accept h2{font-size:31px;font-weight:700;line-height:38px;color:var(--ink)}
.accept .cta{font-size:19px;font-style:italic;line-height:30px;color:var(--ink)}
.accept .cta b{color:var(--pink);font-weight:700}
.illustration{left:91px;top:1135px;width:437px;height:270px;border-radius:8px;background:linear-gradient(160deg,var(--pink-6),var(--pink-5) 60%,var(--pink-4))}
.logo-block{left:91px;top:1420px;width:437px;display:flex;align-items:center;justify-content:center;gap:12px;font-size:36px;font-weight:700;color:var(--mark);line-height:1;white-space:nowrap}
.logo-block .brand-dot{width:18px;height:18px}
.about-copy{left:581px;top:1091px;width:525px;font-size:14.6px;line-height:23px;text-align:justify}
.about-copy p+p{margin-top:23px}
.about-copy b{font-style:italic;color:var(--ink)}
.decor{left:360px;top:1510px;width:840px;height:700px;background:radial-gradient(ellipse at 60% 40%,rgba(241,164,206,.28),rgba(252,237,246,0) 70%)}
.help{left:0;top:1630px;width:1200px;text-align:center}
.help h2{font-size:31px;font-weight:700;color:var(--ink);line-height:40px}
.help p{font-size:30px;font-style:italic;color:var(--pink);line-height:38px}
.cards{left:91px;top:1761px;display:flex;gap:32px}
.card{width:230px;height:396px;background:var(--card);border-radius:22px;box-shadow:0 4px 14px rgba(0,0,0,.08);padding:32px 28px 0;position:relative}
.card h3{font-size:18.5px;font-weight:700;color:var(--ink);text-align:center;white-space:nowrap;margin-bottom:10px}
.card p{font-size:14.4px;line-height:17.5px;text-align:justify;color:var(--text)}
.card .btn{position:absolute;left:56px;top:324px;width:117px;height:40px;border-radius:6px;background:var(--pink);color:var(--white);font-size:13.5px;font-weight:600;display:flex;align-items:center;justify-content:center}
.footer-wave{left:0;top:2195px}
.footer-nav{left:154px;top:2374px;display:flex;gap:55px;font-size:19px;font-weight:700;color:var(--pink-5)}
.plans{left:120px;top:2440px;width:1000px;font-size:19.5px;line-height:33px;text-align:center;color:var(--pink-5)}
.bottom-bar{left:0;top:2658px;width:1200px;height:74px;background:var(--dark);display:flex;align-items:center;justify-content:center;gap:64px;color:var(--white);font-size:15px}
.bottom-bar span{display:flex;align-items:center;gap:14px}
</style>
</head>
<body>

<svg class="abs top-wave" width="1200" height="260" viewBox="0 0 1200 260" aria-hidden="true">
  <path d="M150 0 C380 70 880 50 1060 120 C1130 150 1175 200 1200 245 L1200 0 Z" fill="var(--pink)"/>
</svg>

<div class="abs contact-bar">
  <span><svg width="16" height="16" viewBox="0 0 24 24"><path d="M6.6 10.8a15 15 0 0 0 6.6 6.6l2.2-2.2a1 1 0 0 1 1-.25 11.4 11.4 0 0 0 3.6.57 1 1 0 0 1 1 1V20a1 1 0 0 1-1 1A17 17 0 0 1 3 4a1 1 0 0 1 1-1h3.5a1 1 0 0 1 1 1c0 1.25.2 2.45.57 3.6a1 1 0 0 1-.25 1z" fill="var(--pink)"/></svg>(555) 014-2290</span>
  <span><svg width="16" height="14" viewBox="0 0 24 20"><rect x="1" y="2" width="22" height="16" rx="2" fill="var(--pink)"/><path d="M2 4l10 7 10-7" stroke="#fff" stroke-width="2" fill="none"/></svg>hello@meadowcrestwomens.com</span>
  <span><svg width="13" height="17" viewBox="0 0 16 22"><path d="M8 0a8 8 0 0 0-8 8c0 6 8 14 8 14s8-8 8-14a8 8 0 0 0-8-8z" fill="var(--pink)"/><circle cx="8" cy="8" r="3" fill="#fff"/></svg>4180 Linden Grove Road, Suite 210, Fairhaven, CA 92500</span>
  <span><svg width="15" height="16" viewBox="0 0 20 20"><rect x="1" y="3" width="18" height="16" rx="2" fill="var(--pink)"/><rect x="4" y="6" width="5" height="10" fill="#fff"/><rect x="11" y="7" width="5" height="2" fill="#fff"/><rect x="11" y="11" width="5" height="2" fill="#fff"/></svg>555-014-2291</span>
</div>

<div class="abs brand"><span class="brand-dot"></span>Meadowcrest Women's</div>

<nav class="abs nav"><span>HOME</span><span>SERVICES</span><span>RESOURCES</span><span>ABOUT US</span><span>CONTACT</span></nav>

<section class="welcome">
  <h1 class="abs">WELCOME TO<br>MEADOWCREST,<br>FAIRHAVEN, CA</h1>
  <div class="abs welcome-copy">
    <p>At Meadowcrest Women's in Fairhaven, California, we believe better health starts when the patient is educated. For this reason, we take time to listen to our patients concerns, explain each option available, and to answer any questions our patients may have so that they can make informed decisions. At Meadowcrest Women's, our providers tailor every procedure performed and treatment option recommended to meet the specific needs of our patients. We remain up-to-date on the latest technology and practice guidelines for women’s health.</p>
    <p>Our medical providers will take time to give you the personalized health care you deserve. This includes taking time to listen to you and screening you for problems to help ensure that any health issues are diagnosed and treated as early as possible.</p>
  </div>
  <div class="abs portrait" role="img" aria-label="Portrait photo of a smiling physician in navy scrubs, framed in a pink circle"></div>
</section>

<section>
  <div class="abs accept">
    <div class="kicker">Better Health Starts Here!</div>
    <h2>NOW ACCEPTING NEW PATIENTS</h2>
    <div class="cta"><b>Click Here</b> for an Appointment &nbsp;or <b>Call Us At (555) 014-2290</b></div>
  </div>
  <div class="abs illustration" role="img" aria-label="Line illustration of a doctor with a tablet talking with a patient"></div>
  <div class="abs logo-block"><span class="brand-dot"></span>Meadowcrest Women's</div>
  <div class="abs about-copy">
    <p>Meadowcrest Women's offers you the best care possible in a personalized setting. We are currently accepting patients. Call our office now to make an appointment.</p>
    <p>Meadowcrest Women's (located near Meadow Springs Hospital in Fairhaven, CA) is a medical office that specializes in Christ-centered healthcare for women of all ages. <b>Our team of exclusively female providers</b> have years of experience taking care of women with a variety of pregnancy and gynecology concerns.</p>
    <p>Whether you need a routine examination, help during your pregnancy, have questions on birth control, or another female concern, we offer the best care possible for our patients. That is why better health starts here.</p>
    <p>Our office provides you with an environment where you can feel comfortable and where you know you will be in good hands. Our providers are leaders women’s health. Dr. Halvorsen is a board certified obstetrician and gynecologist. Dr. Marlowe is a board eligible obstetrician and gynecologist.</p>
  </div>
</section>

<div class="abs decor" role="img" aria-label="Faint pink line drawing of women in profile as a background decoration"></div>

<section>
  <div class="abs help">
    <h2>HOW CAN WE HELP YOU?</h2>
    <p>Health Services Offered</p>
  </div>
  <div class="abs cards">
    <article class="card">
      <h3>PREGNANCY CARE</h3>
      <p>Receiving regular care in pregnancy is important for the health of both you and your baby. Our obstetrcians work with you every step of the way during your pregnancy and delivery to make sure your individual needs are met and co ensure this special journey is a memorable one.</p>
      <span class="btn">Learn More »</span>
    </article>
    <article class="card">
      <h3>BIRTH CONTROL</h3>
      <p>Our gynecologists are knowledgeable on all forms of birth control including the IUD, the arm implant, vaginal ringinsertion, birth control pills, and more! We would love to work with you to determine the best option for you and your lifestyle.</p>
      <span class="btn">Learn More »</span>
    </article>
    <article class="card">
      <h3>WELL WOMAN EXAMS</h3>
      <p>Our providers will help you to stay healthy by performing a physical exam on you annually. We will screen you for multiple health conditions that may pose a risk to you. This includes screening you for cancerous conditions of the breast, ovaries and cervix.</p>
      <span class="btn">Learn More »</span>
    </article>
    <article class="card">
      <h3>WOMEN'S HEALTH</h3>
      <p>Whether you are dealing with painful or irregular periods, fibroids, or other women's health i ssues, we can help. We offer a variety of the most up-to-date treatment options to help you regain your lifestyle.</p>
      <span class="btn">Learn More »</span>
    </article>
  </div>
</section>

<footer>
  <svg class="abs footer-wave" width="1200" height="463" viewBox="0 0 1200 463" aria-hidden="true">
    <path d="M0 110 C300 60 500 110 800 100 C1000 92 1130 60 1200 0 L1200 463 L0 463 Z" fill="var(--pink)"/>
  </svg>
  <nav class="abs footer-nav"><span>HOME</span><span>ABOUT US</span><span>NEWS</span><span>PATIENT RESOURCES</span><span>PRIVACY POLICY</span><span>CONTACT US</span></nav>
  <p class="abs plans">Brightpath - Valley Direct - Oakline Care North - Oakline Care East - CARELINK - Marrow Bay Medical Group - Servicemember Prime - Canyon Physicians - Northvale Open Access - Ridgeline Select - Blue Harbor - Cedarpoint - Cedarpoint Local Plus - Veterans Family Plan - EBSA - FEBA - Fernway Health - Larkspur Health - Steelworkers Trust Fund - Builders Health &amp; Welfare Fund - Postal Carriers - Crane Operators - Metal Trades - Servicemember Select - UnionWell Health - Retail Workers Plan - BMA - Oakline Care South</p>
  <div class="abs bottom-bar">
    <span><svg width="26" height="26" viewBox="0 0 24 24"><path d="M6.6 10.8a15 15 0 0 0 6.6 6.6l2.2-2.2a1 1 0 0 1 1-.25 11.4 11.4 0 0 0 3.6.57 1 1 0 0 1 1 1V20a1 1 0 0 1-1 1A17 17 0 0 1 3 4a1 1 0 0 1 1-1h3.5a1 1 0 0 1 1 1c0 1.25.2 2.45.57 3.6a1 1 0 0 1-.25 1z" fill="var(--pink)"/></svg>(555) 014-2290</span>
    <span><svg width="26" height="20" viewBox="0 0 24 20"><rect x="1" y="2" width="22" height="16" rx="2" fill="var(--pink)"/><path d="M2 4l10 7 10-7" stroke="var(--dark)" stroke-width="2" fill="none"/></svg>hello@meadowcrestwomens.com</span>
    <span><svg width="20" height="28" viewBox="0 0 16 22"><path d="M8 0a8 8 0 0 0-8 8c0 6 8 14 8 14s8-8 8-14a8 8 0 0 0-8-8z" fill="var(--pink)"/><circle cx="8" cy="8" r="3" fill="var(--dark)"/></svg>4180 Linden Grove Road, Suite 210, Fairhaven, CA 92500</span>
  </div>
</footer>

</body>
</html>
```